New Interrior Decoration company needs new website

We need a website for our new company specialising in interior decoration to residential and commercial markets.
We supply and install decorative and printed films for office and home decoration such as feature walls.
We would like to keep the design simple and clean.

Target Market(s)

Architects and interior designaers

Industry/Entity Type

It Company

Number of Pages Required

5+ page

Font styles to use
Sans Serif

Requirements
Must have
• Home page,
• Services/products page (split into commercial and residential)
• Gallery (split into commercial and residential)
• contact form and page
Nice to have
• Very clean and minimalistic design.

```html
<!DOCTYPE html>
<html lang="en">
<head>
<meta charset="utf-8">
<title>NM Facet Interiors</title>
<link href="https://fonts.googleapis.com/css2?family=Lato:ital,wght@0,400;0,700;1,700&family=Arimo:wght@400;700&display=swap" rel="stylesheet">
<style>
:root{
  --blue:#0d5ab9;
  --ink:#1d1d1d;
  --body:#8a8a8a;
  --soft:#efefef;
  --white:#ffffff;
  --footer:#333333;
  --footer-deep:#222222;
  --footer-text:#c9c9c9;
  --tab:#e4e4e4;
}
*{margin:0;padding:0;box-sizing:border-box}
html,body{width:1200px;height:3303px;overflow:hidden;background:var(--white)}
body{position:relative;font-family:"Arimo",Arial,sans-serif;color:var(--body)}
.abs{position:absolute}
.heading{font-family:"Lato",Arial,sans-serif;color:var(--ink);font-weight:400}
.btn{position:absolute;background:var(--blue);color:var(--white);font-family:"Lato",Arial,sans-serif;font-size:21px;display:flex;align-items:center;justify-content:center;border-radius:3px;letter-spacing:.3px}

/* header */
.site-header{top:0;left:0;width:1200px;height:106px;background:var(--white)}
.brand{left:77px;top:22px;display:flex;align-items:center;gap:14px}
.brand-square{width:58px;height:58px;background:var(--blue)}
.brand-name{font-family:"Lato",Arial,sans-serif;font-weight:700;font-size:34px;line-height:32px;color:var(--ink);letter-spacing:.5px}
.nav a{position:absolute;top:29px;height:52px;line-height:52px;font-family:"Lato",Arial,sans-serif;font-size:17px;color:var(--ink);text-decoration:none}
.nav .active{background:var(--blue);color:var(--white);border-radius:3px;width:92px;text-align:center}

/* hero */
.hero{top:106px;left:0;width:1200px;height:577px;background:linear-gradient(180deg,#5c6b63 0%,#4e5c55 70%,#7d8782 78%,#9aa29f 100%)}
.hero-text{top:228px;left:0;width:1200px;text-align:center;font-family:"Lato",Arial,sans-serif;font-style:italic;font-weight:700;font-size:40px;line-height:52px;color:var(--white);text-shadow:0 2px 4px rgba(0,0,0,.45)}
.hero-arrow{top:256px;width:52px;height:52px;border:2px solid rgba(255,255,255,.6);border-radius:50%}

/* welcome */
.welcome{top:683px;left:0;width:1200px;height:477px}
.mark{left:564px;top:66px;width:72px;height:48px;background:var(--blue)}
.welcome h1{position:absolute;top:124px;width:1200px;text-align:center;font-size:44px}
.welcome p{position:absolute;top:188px;left:140px;width:920px;text-align:center;font-size:14px;line-height:27px}

/* services */
.services{top:1160px;left:0;width:1200px;height:806px;background:var(--soft)}
.section-title{position:absolute;width:1200px;text-align:center;font-size:40px}
.services .intro{position:absolute;top:118px;left:220px;width:760px;text-align:center;font-size:14px;line-height:26px}
.service-img{position:absolute}
.service-title{position:absolute;font-size:30px}
.service-text{position:absolute;width:500px;font-size:14px;line-height:27px}

/* gallery */
.gallery{top:1966px;left:0;width:1200px;height:764px;background:var(--white)}
.tab{position:absolute;top:143px;height:42px;font-size:16px;display:flex;align-items:center;justify-content:center;background:var(--tab);color:#555}
.tab.on{background:var(--blue);color:var(--white)}
.tile{position:absolute}
.feature-tile{display:flex;flex-direction:column;align-items:center;justify-content:center;color:var(--white)}
.feature-tile b{font-size:21px;font-weight:700}
.feature-tile span{font-size:17px;margin-top:4px}

/* testimonial */
.testimonial{top:2730px;left:0;width:1200px;height:271px;background:var(--soft)}
.avatar{left:214px;top:117px;width:88px;height:88px;border-radius:50%;border:3px solid var(--white);box-shadow:0 0 0 2px #c8c8c8;background:linear-gradient(180deg,#c7b08e,#e9d9c4)}
.quote{left:321px;top:126px;width:680px;font-size:16px;line-height:28px;color:#777}
.client{left:321px;top:195px;font-family:"Lato",Arial,sans-serif;font-weight:700;font-size:14px;color:var(--blue);display:flex;align-items:center;gap:14px}
.client i{display:block;width:26px;height:2px;background:var(--blue)}

/* footer */
.site-footer{top:3001px;left:0;width:1200px;height:238px;background:var(--footer)}
.col-title{position:absolute;top:36px;font-family:"Lato",Arial,sans-serif;font-weight:700;font-size:15px;color:var(--blue)}
.links{position:absolute;left:77px;top:72px;list-style:none}
.links li{font-size:14px;color:var(--footer-text);line-height:27px;display:flex;align-items:center;gap:18px}
.links li::before{content:"";width:7px;height:7px;border-radius:50%;background:var(--blue)}
.contact-row{position:absolute;left:310px;display:flex;gap:14px;font-size:13px;line-height:22px;color:var(--footer-text)}
.contact-row svg{flex:none}
.news-note{left:599px;top:76px;font-size:13px;color:var(--footer-text)}
.email-field{left:594px;top:109px;width:249px;height:45px;border:1px solid #555;padding-left:14px;font-size:12px;color:#888;display:flex;align-items:center}
.subscribe{left:594px;top:164px;width:249px;height:45px;font-size:17px}
.foot-brand{left:874px;top:30px;display:flex;align-items:center;gap:12px}
.foot-brand .brand-square{width:46px;height:46px}
.foot-brand .brand-name{font-size:25px;line-height:24px;color:var(--blue)}
.foot-rule{left:900px;top:103px;width:200px;height:1px;background:#555}
.social{top:126px;width:40px;height:40px;border-radius:2px}
.bottom-bar{top:3239px;left:0;width:1200px;height:64px;background:var(--footer-deep);display:flex;align-items:center;justify-content:center;font-size:14px;color:var(--footer-text)}
.bottom-bar span{color:var(--blue)}
</style>
</head>
<body>

<header class="site-header abs">
  <div class="brand abs">
    <div class="brand-square"></div>
    <div class="brand-name">NM FACET<br>INTERIORS</div>
  </div>
  <nav class="nav">
    <a class="active" style="left:511px">HOME</a>
    <a style="left:638px">ABOUT US</a>
    <a style="left:768px">SERVICES</a>
    <a style="left:907px">GALLERY</a>
    <a style="left:1035px">CONTACT</a>
  </nav>
</header>

<section class="hero abs" role="img" aria-label="Styled room with a grey concrete wall, pendant lamp, framed art and a wooden sideboard">
  <div class="hero-text abs">WE ARE SPECIALISING IN INTERIOR DECORATION FOR<br>RESIDENTIAL &amp; COMMERCIAL MARKETS.</div>
  <svg class="hero-arrow abs" style="left:11px" viewBox="0 0 52 52"><path d="M29 17 L20 26 L29 35" fill="none" stroke="rgba(255,255,255,.75)" stroke-width="2"/></svg>
  <svg class="hero-arrow abs" style="left:1137px" viewBox="0 0 52 52"><path d="M23 17 L32 26 L23 35" fill="none" stroke="rgba(255,255,255,.75)" stroke-width="2"/></svg>
</section>

<section class="welcome abs">
  <div class="mark abs"></div>
  <h1 class="heading">WELCOME TO NM FACET INTERIORS</h1>
  <p>Lorem Ipsum is simply dummy text of the printing and typesetting industry. Lorem Ipsum has been the industry's standard dummy text ever since the 1500s, when an unknown printer took a galley of type and scrambled it to make a type specimen book. It has survived not only five centuries, but also the leap into electronic typesetting.<br>Lorem Ipsum is simply dummy text of the printing and typesetting industry. Lorem Ipsum has been the industry's standard dummy text ever since the 1500s, when an unknown printer took a galley of type and scrambled it to make a type specimen book. It has survived not only five centuries, but also the leap into electronic</p>
  <div class="btn" style="left:506px;top:354px;width:188px;height:62px">KNOW MORE</div>
</section>

<section class="services abs">
  <h2 class="heading section-title" style="top:60px">OUR SERVICE</h2>
  <p class="intro">orem Ipsum is simply dummy text of the printing and typesetting industry. Lorem Ipsum has been the industry's standard dummy text ever since the 1500s, when</p>

  <div class="service-img" style="left:77px;top:205px;width:491px;height:225px;background:linear-gradient(180deg,#e6e6e6 0%,#d9b3ae 50%,#e6e6e6 100%)" role="img" aria-label="Living room illustration with a red feature wall and a dark sofa with colourful cushions"></div>
  <h3 class="heading service-title" style="left:608px;top:207px">RESIDENTIAL DESIGN</h3>
  <p class="service-text" style="left:608px;top:253px">Lorem Ipsum is simply dummy text of the printing and typesetting ind ustry. Lorem Ipsum has been the industry's standard dummy text ever since the 1500s, when an unknown printer took a galley of type and scra mbled it to make a type specimen book.</p>
  <div class="btn" style="left:608px;top:375px;width:185px;height:59px">KNOW MORE</div>

  <h3 class="heading service-title" style="left:77px;top:491px">COMMERCIAL DESIGN</h3>
  <p class="service-text" style="left:77px;top:539px">Lorem Ipsum is simply dummy text of the printing and typesetting ind ustry. Lorem Ipsum has been the industry's standard dummy text ever since the 1500s, when an unknown printer took a galley of type and scra mbled it to make a type specimen book.</p>
  <div class="btn" style="left:77px;top:663px;width:187px;height:62px">KNOW MORE</div>
  <div class="service-img" style="left:687px;top:480px;width:436px;height:271px;background:linear-gradient(180deg,#d4d4d4 0%,#a9a9a9 55%,#c9c9c9 100%)" role="img" aria-label="3D cutaway render of a furnished office floor"></div>
</section>

<section class="gallery abs">
  <h2 class="heading section-title" style="top:62px">OUR GALLERY</h2>
  <div class="tab on" style="left:233px;width:256px">ALL INTERIORS DESIGNS</div>
  <div class="tab" style="left:500px;width:233px">COMMERCIAL DESIGN</div>
  <div class="tab" style="left:740px;width:224px">RESIDENTIAL DESIGN</div>

  <div class="tile feature-tile" style="left:77px;top:214px;width:244px;height:416px;background:linear-gradient(160deg,#2e7ad6,#0d4fa6)" role="img" aria-label="Blue-toned residential interior"><b>DREAM HOUSE</b><span>Residential</span></div>
  <div class="tile" style="left:335px;top:214px;width:259px;height:202px;background:linear-gradient(180deg,#d6e37a,#eeeeea)" role="img" aria-label="Lounge with a lime patterned feature wall"></div>
  <div class="tile" style="left:335px;top:427px;width:259px;height:203px;background:linear-gradient(180deg,#b79a6a,#c0584a 70%,#d8d2c8)" role="img" aria-label="Room with wood-panel feature wall and red chairs"></div>
  <div class="tile" style="left:605px;top:214px;width:260px;height:202px;background:linear-gradient(180deg,#6e3b47,#c9a9a0 80%,#e8e4df)" role="img" aria-label="Living room with a plum wall and white sofa"></div>
  <div class="tile" style="left:605px;top:427px;width:260px;height:203px;background:linear-gradient(180deg,#7a7550,#a7a07a 70%,#c7c1a8)" role="img" aria-label="Olive-toned room with a low cabinet"></div>
  <div class="tile" style="left:878px;top:214px;width:245px;height:416px;background:linear-gradient(90deg,#f1f1ef,#dcdcd8 60%,#8b8f95)" role="img" aria-label="Office corridor with printed circle film on a glass wall"></div>

  <div class="btn" style="left:506px;top:643px;width:188px;height:60px">VIEW ALL</div>
</section>

<section class="testimonial abs">
  <h2 class="heading section-title" style="top:60px">WHAT OUR CLIENT SAY</h2>
  <svg class="abs" style="left:130px;top:140px" width="26" height="46" viewBox="0 0 26 46"><path d="M22 2 L3 23 L22 44" fill="none" stroke="#bbbbbb" stroke-width="2"/></svg>
  <svg class="abs" style="left:1045px;top:140px" width="26" height="46" viewBox="0 0 26 46"><path d="M4 2 L23 23 L4 44" fill="none" stroke="#bbbbbb" stroke-width="2"/></svg>
  <div class="avatar abs" role="img" aria-label="Client portrait"></div>
  <p class="quote abs">Lorem Ipsum is simply dummy text of the printing and typesetting industry. Lorem Ipsum has been the industry's standard dummy text ever since the 1500s</p>
  <div class="client abs"><i></i>CLIENT NAME</div>
</section>

<footer class="site-footer abs">
  <div class="col-title" style="left:77px">USEFULL LINKS</div>
  <ul class="links">
    <li>Home</li><li>About Us</li><li>Services</li><li>Gallery</li><li>Contact</li>
  </ul>

  <div class="col-title" style="left:310px">GET IN TOUCH</div>
  <div class="contact-row" style="top:73px">
    <svg width="18" height="22" viewBox="0 0 18 22"><path d="M9 1 V21 M2 5 H16 M2 11 H16 M2 17 H16" stroke="#0d5ab9" stroke-width="2.4"/></svg>
    <span>Lorem Ipsum is simple dummy text<br>of printing and type srettin</span>
  </div>
  <div class="contact-row" style="top:131px">
    <svg width="18" height="14" viewBox="0 0 18 14"><rect x="1" y="1" width="16" height="12" fill="#0d5ab9"/><path d="M1 1 L9 8 L17 1" fill="none" stroke="#333" stroke-width="1.5"/></svg>
    <span>info@facetinteriors.com</span>
  </div>
  <div class="contact-row" style="top:170px">
    <svg width="18" height="18" viewBox="0 0 18 18"><path d="M4 1 L7 5 L5 7 C6 10 8 12 11 13 L13 11 L17 14 L15 17 C8 17 1 10 1 3 Z" fill="#0d5ab9"/></svg>
    <span>123 456 7890</span>
  </div>

  <div class="col-title" style="left:599px">NEWSLETTER</div>
  <div class="news-note abs">Subscribe to the newsletter</div>
  <div class="email-field abs">Enter Your Email *</div>
  <div class="btn subscribe">SUBSCRIBR</div>

  <div class="foot-brand abs">
    <div class="brand-square"></div>
    <div class="brand-name">NM FACET<br>INTERIORS</div>
  </div>
  <div class="foot-rule abs"></div>
  <div class="social abs" style="left:927px;background:var(--blue)" role="img" aria-label="Social link"></div>
  <div class="social abs" style="left:978px;background:#8a8a8a" role="img" aria-label="Social link"></div>
  <div class="social abs" style="left:1028px;background:#8a8a8a" role="img" aria-label="Social link"></div>
</footer>

<div class="bottom-bar abs">©<span>FacetInteriors</span>&nbsp;- 2016. All rights reserved.</div>

</body>
</html>
```